Real Estate Sign Project

We need a Real Estate sign that promotes the property being listed and our company and agent listing the property. The images need to be able to be swapped out so we can use the template for each listing we have. I have a sample from another company that shows what were are trying to accomplish. Would want ours to be unique using our logo and the colors in our logo. We would like to not have to use a rider. Would want agents name and phone number to be part of the 36" x 24" sign.

Industry/Entity Type

Real Estate

Requirements
Must have
• Sign dimensions are 36 inches by 24 inches (36" across and 24" up down). Use example.of.sign.we.want.jpg as the direction we want to go but with a different layout and our logo and colors. This would be just a template that we can swap out new pictures, address, price, website, agents contact info for each home we are listing. Like the idea of the pictures bleeding off the sides. Please use free stock photos for the home images as we will be changing these out for each listing. Please incorporate all info including agents info into the one sign. File must be layered so we can change the pictures, price, website, agent, etc. We use GIMP (.xcf) file

```html
<!DOCTYPE html>
<html lang="en">
<head>
<meta charset="utf-8">
<title>Harborline Realty – Listing Sign</title>
<link href="https://fonts.googleapis.com/css2?family=Open+Sans:wght@400;600;700;800&display=swap" rel="stylesheet">
<style>
  :root {
    --navy: #1f3370;
    --navy-deep: #17285c;
    --orange: #e8561c;
    --orange-light: #f28a2e;
    --grey-band: #8a8a8a;
    --grey-band-light: #d9d9d9;
    --white: #ffffff;
    --panel-light: #f4f5f8;
    --page: #ffffff;
  }
  * { margin: 0; padding: 0; box-sizing: border-box; }
  html, body {
    width: 827px; height: 1200px; overflow: hidden;
    background: var(--page);
    font-family: "Open Sans", Arial, sans-serif;
  }
  .canvas { position: relative; width: 827px; height: 1200px; }

  /* Top header panel */
  .sale-panel {
    position: absolute; left: 142px; top: 142px; width: 484px; height: 80px;
    border-radius: 8px; overflow: hidden;
    background: linear-gradient(90deg, var(--white) 0%, #e6e9f0 30%, #6f7fa6 65%, var(--navy) 100%);
  }
  .sale-panel::before {
    content: ""; position: absolute; left: 0; top: 0; right: 0; height: 5px;
    background: linear-gradient(90deg, var(--orange-light), var(--orange));
  }
  .sale-brand {
    position: absolute; left: 10px; top: 28px; width: 80px;
    display: flex; align-items: center; gap: 4px;
    color: var(--navy); font-weight: 800; font-size: 11px; line-height: 1.05;
  }
  .brand-dot {
    width: 14px; height: 14px; border-radius: 50%; background: var(--orange); flex: none;
  }
  .sale-title {
    position: absolute; left: 96px; top: 2px; right: 14px;
    color: var(--white); font-weight: 700; font-size: 70px; line-height: 80px;
    letter-spacing: 1px; white-space: nowrap; text-align: center;
  }

  /* Main listing panel */
  .listing-panel {
    position: absolute; left: 142px; top: 318px; width: 484px; height: 322px;
    border-radius: 10px; overflow: hidden;
    background: linear-gradient(180deg, var(--white) 0%, var(--panel-light) 100%);
    border: 1px solid #c9ccd4;
  }
  .listing-header {
    position: absolute; left: 0; top: 0; width: 100%; height: 35px;
    background: linear-gradient(90deg, var(--grey-band) 0%, #b3b3b3 45%, var(--grey-band-light) 70%, var(--white) 100%);
  }
  .listing-address {
    position: absolute; left: 16px; top: 2px;
    color: var(--white); font-weight: 700; font-size: 23px; line-height: 31px;
  }
  .listing-price {
    position: absolute; right: 16px; top: 0;
    color: var(--navy); font-weight: 800; font-size: 30px; line-height: 33px;
  }

  .photo { position: absolute; }
  .photo-exterior { left: 14px; top: 49px; width: 225px; height: 149px;
    background: linear-gradient(180deg, #9ec17a 0%, #8a6a52 45%, #6f9d3f 100%); }
  .photo-kitchen { left: 248px; top: 48px; width: 107px; height: 70px;
    background: linear-gradient(135deg, #c89a6a, #7a4a28); }
  .photo-living { left: 363px; top: 48px; width: 107px; height: 70px;
    background: linear-gradient(135deg, #d8c7aa, #6e4a34); }
  .photo-bedroom { left: 248px; top: 127px; width: 107px; height: 71px;
    background: linear-gradient(135deg, #e6e0d4, #5c4636); }
  .photo-bath { left: 363px; top: 127px; width: 107px; height: 71px;
    background: linear-gradient(135deg, #efe8da, #b59c7a); }

  .features {
    position: absolute; left: 120px; top: 200px; width: 360px;
    display: grid; grid-template-columns: 168px 1fr; row-gap: 0;
    list-style: none;
    color: var(--navy); font-weight: 700; font-size: 19px; line-height: 23px;
  }
  .features li { display: flex; align-items: center; gap: 8px; }
  .features li::before {
    content: ""; width: 9px; height: 9px; border-radius: 50%; background: var(--orange); flex: none;
  }

  .orange-rule {
    position: absolute; left: 0; top: 250px; width: 120px; height: 3px;
    background: var(--orange);
  }
  .footer-brand {
    position: absolute; left: 12px; top: 262px; width: 110px;
    display: flex; align-items: center; gap: 6px;
    color: var(--navy); font-weight: 800; font-size: 15px; line-height: 1.1;
  }
  .footer-brand .brand-dot { width: 20px; height: 20px; }

  .agent-band {
    position: absolute; left: 118px; top: 256px; right: 0; bottom: 0;
    background: linear-gradient(90deg, rgba(31,51,112,0) 0%, #7c8bb0 18%, var(--navy) 45%, var(--navy-deep) 100%);
    text-align: right; padding: 3px 14px 0 0; color: var(--white);
  }
  .agent-name { font-weight: 700; font-size: 23px; line-height: 26px; }
  .agent-phone { font-weight: 400; font-size: 20px; line-height: 22px; }
  .agent-web { font-weight: 400; font-size: 12.5px; line-height: 16px; }
</style>
</head>
<body>
<main class="canvas">

  <section class="sale-panel">
    <div class="sale-brand"><span class="brand-dot"></span><span>Harborline Realty</span></div>
    <h1 class="sale-title">FOR SALE</h1>
  </section>

  <section class="listing-panel">
    <header class="listing-header">
      <div class="listing-address">1870 Linden Ave</div>
      <div class="listing-price">$360,000</div>
    </header>

    <div class="photo photo-exterior" role="img" aria-label="Exterior photo of a brick colonial home with lawn"></div>
    <div class="photo photo-kitchen" role="img" aria-label="Kitchen with wooden cabinets"></div>
    <div class="photo photo-living" role="img" aria-label="Living room with leather furniture"></div>
    <div class="photo photo-bedroom" role="img" aria-label="Bedroom with sitting area"></div>
    <div class="photo photo-bath" role="img" aria-label="Bathroom with soaking tub"></div>

    <ul class="features">
      <li>4 Bedroom</li>
      <li>3270 Finished SF</li>
      <li>3.5 Baths</li>
      <li>2 Car Garage</li>
    </ul>

    <div class="orange-rule"></div>
    <div class="agent-band">
      <div class="agent-name">DANA WHITFIELD</div>
      <div class="agent-phone">555-014-2290</div>
      <div class="agent-web">www.harborlinehomes.com</div>
    </div>
    <div class="footer-brand"><span class="brand-dot"></span><span>Harborline Realty</span></div>
  </section>

</main>
</body>
</html>
```